Sunset Harbor Living Web Page

We need a web page design that has two intro pages - first being a 'home page', then a link to the second page that has the 'content tabs' and a 'call to action' (see below).

The business helps people that wish to retire to S.E.Asia (Thailand, Malaysia, Indonesia,The Philippines etc) - to enjoy the lifestyle and the remaining years of their lives. What attracts S.E.Asia to many people is the lower cost, the atmoshpere and beauty of the tropics and the vibrancy of the various countries.

People that are wishing to make the most of their retirement and are adventurous at a great bargain compared to the cost of their own countries will be interested.

We help them achieve this - visa, financials (tax, gov't payments etc), introduce them to the right people for property, clubs, retirement facilities, insurance and so forth.

Therefore we are providing an extremely wide ranging service and this site will provide broad but general information only - with a call to action to come and see us for more specific information and how we can help them specifically.

This site will be predominantly for travel and lifestyle, it will be linked with another financial services (financial planning) site later down the track.

The colour scheme is dark green and blue - as per the attached logo design. Photos and background just think lifestyle and S.E.Asia - beaches/mountains/water/recreational activities for retirees.

Target market is mostly those coming up to retirement to those that are already retired. But we also expect to have some interest with younger people that would like to find out more and plan for the future. So a broad age group but I would say mostly 40-70 yrs old.

On the first (Home) page we would like our company name 'Sunset Harbor Living', our logo (which will be on all pages) and a statement such as: “Imagine a retirement where your dreams are brought to life, and you have never felt more alive. Let us show you how”. Then a link to the second page.

We would like an uncluttered site. On the second (contents) page the tabs would be:

- Visa
- Property
- Financials
- Travel
- Insurance & Healthcare
- Medical Tourism
- Cost of living
- Weekly Blogs and articles
- Sunset Harbor Living story

We would also like a call to action on the second page - asking them to leave their contact details if they wish to learn more or sign up to our weekly newsletter/blog.

We are open to suggestions and your imaginations.

Thank you
Malcolm

Font styles to use
Serif
Script

Colors
0255a3
3377b5
00a990
9bcb3c
abd036
33b8a4
85abd2
cadf82
86cfc6

Requirements
Must have
• I have been asked by the web designer to receive a 'Web Font' so that we can 'get off of Zentrofy'. Hope that makes sense.

```html
<!DOCTYPE html>
<html lang="en">
<head>
<meta charset="utf-8">
<title>Sunset Harbor Living — Home</title>
<link rel="stylesheet" href="https://fonts.googleapis.com/css2?family=Playfair+Display:wght@400;700&family=Yellowtail&family=Quicksand:wght@600&display=swap">
<style>
  :root {
    --blue-deep: #0255a3;
    --blue-mid: #3377b5;
    --teal: #00a990;
    --green: #9bcb3c;
    --lime: #abd036;
    --teal-soft: #33b8a4;
    --blue-soft: #85abd2;
    --green-pale: #cadf82;
    --aqua-pale: #86cfc6;
    --button: #0fae6a;
    --white: #ffffff;
  }
  * { margin: 0; padding: 0; box-sizing: border-box; }
  html, body { width: 1200px; height: 810px; overflow: hidden; background: #0d1c33; }
  .hero { position: relative; width: 1200px; height: 810px; overflow: hidden; }
  .hero-scene {
    position: absolute; inset: 0;
    background:
      radial-gradient(ellipse 330px 330px at 520px 420px, rgba(52,96,40,0.95) 0%, rgba(40,72,36,0.85) 60%, rgba(40,72,36,0) 100%),
      linear-gradient(180deg, #152a4e 0%, #22406a 35%, #35557a 58%, #1e6a78 76%, #1a8a86 88%, #16675f 100%);
  }
  .hero-scene::after { content: ""; position: absolute; inset: 0; background: rgba(5,15,30,0.28); }
  .brand { position: absolute; left: 0; top: 40px; width: 1200px; text-align: center; }
  .brand-mark { width: 82px; height: 82px; border-radius: 50%; background: var(--teal); margin: 0 auto 34px; }
  .brand-name { font-family: "Playfair Display", serif; font-weight: 700; font-size: 36px; color: var(--blue-soft); line-height: 1; }
  .headline { position: absolute; inset: 0; }
  .line { position: absolute; line-height: 1; white-space: nowrap; }
  .serif { font-family: "Playfair Display", serif; color: var(--white); }
  .script { font-family: "Yellowtail", cursive; }
  .imagine { left: 90px; top: 252px; font-size: 104px; }
  .a { left: 318px; top: 338px; font-size: 50px; }
  .retirement { left: 226px; top: 362px; font-size: 104px; color: var(--teal-soft); }
  .where { left: 394px; top: 450px; font-size: 66px; color: var(--green-pale); }
  .your { left: 462px; top: 500px; font-size: 46px; color: var(--green-pale); }
  .dreams { left: 598px; top: 448px; font-size: 106px; color: var(--lime); }
  .tagline { left: 0; width: 1200px; text-align: center; top: 563px; font-size: 43px; }
  .cta {
    position: absolute; left: 461px; top: 669px; width: 279px; height: 60px;
    background: var(--button); border-radius: 3px; color: var(--white);
    font-family: "Quicksand", sans-serif; font-weight: 600; font-size: 17px;
    display: flex; align-items: center; justify-content: center; text-decoration: none; letter-spacing: 0.2px;
  }
</style>
</head>
<body>
<main class="hero">
  <div class="hero-scene" role="img" aria-label="Tropical limestone island covered in jungle rising from turquoise sea under a deep blue sky, with a small longtail boat"></div>
  <header class="brand">
    <div class="brand-mark"></div>
    <div class="brand-name">Sunset Harbor Living</div>
  </header>
  <h1 class="headline">
    <span class="line serif imagine">Imagine</span>
    <span class="line serif a">a</span>
    <span class="line script retirement">Retirement</span>
    <span class="line script where">where</span>
    <span class="line serif your">your</span>
    <span class="line script dreams">Dreams</span>
    <span class="line serif tagline">Are Brought to Life,and you Have Never Felt More Alive.</span>
  </h1>
  <a class="cta" href="#contents">LET US SHOW YOU HOW</a>
</main>
</body>
</html>
```